BOLD & MINIMALIST DESIGN NEEDED

We want a very bold but minimalistic business card design that is impactful and utilizes both sides of the business card. Our current logo is included for your use.

We want bold fonts and good use of negative space. We don't want the logo to overpower the design.

Target Market(s)

Professionals who are building new commercial buildings.

Industry/Entity Type

Construction

Contact Information for Business Card

Name, Title, email, office phone, cell phone, website

Font styles to use
Serif
Sans Serif

Requirements
Must have
• Bold design!

```html
<!DOCTYPE html>
<html lang="en">
<head>
<meta charset="utf-8">
<title>Ridgeline Design + Build – Business Card</title>
<link rel="stylesheet" href="https://fonts.googleapis.com/css2?family=Poppins:wght@400;500;600;800&display=swap">
<style>
  :root{
    --stage:#2a2a2a;
    --ink:#0b0b0b;
    --paper:#ffffff;
    --green:#7fc41f;
    --green-dark:#5f9e12;
    --grey:#f2f2f2;
  }
  *{box-sizing:border-box;margin:0;padding:0}
  html,body{width:1200px;height:689px;overflow:hidden;background:var(--stage)}
  body{font-family:"Poppins",sans-serif;position:relative}
  .card{position:absolute;top:190px;width:540px;height:309px;border-radius:18px;overflow:hidden}
  .card--back{left:30px;background:var(--ink)}
  .card--front{left:630px;background:var(--paper)}

  /* back */
  .back-brand{position:absolute;left:40px;top:122px;color:var(--paper)}
  .brand-name{font-weight:800;font-size:46px;letter-spacing:1px;line-height:1}
  .brand-rule{height:2px;background:currentColor;margin:6px 0 4px}
  .brand-sub{font-weight:400;font-size:13px;letter-spacing:9px;text-align:right}
  .back-block{position:absolute;right:0;top:0;width:150px;height:309px;background:var(--green)}

  /* front */
  .front-brand{position:absolute;right:32px;top:40px;color:var(--ink);display:flex;align-items:center;gap:10px}
  .front-brand .brand-name{font-size:30px}
  .front-brand .brand-sub{font-size:9px;letter-spacing:6px}
  .brand-dot{width:18px;height:18px;background:var(--green)}
  .person{position:absolute;left:46px;top:118px}
  .person::before{content:"";position:absolute;left:-22px;top:6px;width:12px;height:38px;background:var(--green)}
  .person-name{font-weight:800;font-size:22px;color:var(--ink);line-height:1.1}
  .person-title{font-weight:400;font-size:16px;color:var(--green)}
  .phones{position:absolute;left:46px;bottom:58px;font-size:16px;color:var(--ink);line-height:1.45}
  .online{position:absolute;right:32px;top:140px;font-size:15px;color:var(--ink);line-height:1.5;text-align:right}
  .row{display:flex;align-items:center;gap:8px}
  .online .row{justify-content:flex-end}
  .icon{width:14px;height:14px;flex:none}
  .front-stripes{position:absolute;left:0;bottom:0;width:540px;height:46px}
</style>
</head>
<body>

<section class="card card--back" aria-label="Card back">
  <div class="back-brand">
    <div class="brand-name">RIDGELINE</div>
    <div class="brand-rule"></div>
    <div class="brand-sub">DESIGN + BUILD</div>
  </div>
  <div class="back-block"></div>
</section>

<section class="card card--front" aria-label="Card front">
  <div class="front-brand">
    <span class="brand-dot"></span>
    <div>
      <div class="brand-name">RIDGELINE</div>
      <div class="brand-rule"></div>
      <div class="brand-sub">DESIGN + BUILD</div>
    </div>
  </div>

  <div class="person">
    <div class="person-name">MARCUS HALE</div>
    <div class="person-title">Managing Director</div>
  </div>

  <div class="online">
    <div class="row">info@ridgelinebuild.com
      <svg class="icon" viewBox="0 0 14 14"><rect x="1" y="3" width="12" height="8" fill="var(--green)"/><path d="M1 3l6 5 6-5" fill="none" stroke="#fff" stroke-width="1.2"/></svg>
    </div>
    <div class="row">www.ridgelinebuild.com
      <svg class="icon" viewBox="0 0 14 14"><circle cx="7" cy="7" r="6" fill="none" stroke="var(--green)" stroke-width="1.4"/><path d="M1 7h12M7 1v12" stroke="var(--green)" stroke-width="1.2"/></svg>
    </div>
  </div>

  <div class="phones">
    <div class="row">
      <svg class="icon" viewBox="0 0 14 14"><path d="M3 1l3 3-1.5 1.5a8 8 0 0 0 4 4L10 8l3 3-2 2C6 13 1 8 1 3z" fill="var(--green)"/></svg>
      044-555 210 347
    </div>
    <div class="row">
      <svg class="icon" viewBox="0 0 14 14"><rect x="3.5" y="1" width="7" height="12" rx="1.2" fill="none" stroke="var(--green)" stroke-width="1.4"/><circle cx="7" cy="11" r=".8" fill="var(--green)"/></svg>
      044-555 210 347
    </div>
  </div>

  <svg class="front-stripes" viewBox="0 0 540 46" preserveAspectRatio="none" aria-hidden="true">
    <path d="M300 14L330 0H540V46H300Z" fill="var(--ink)"/>
    <g stroke="var(--green)" stroke-width="1.6">
      <line x1="0" y1="30" x2="300" y2="30"/>
      <line x1="0" y1="34" x2="300" y2="34"/>
      <line x1="0" y1="38" x2="300" y2="38"/>
      <line x1="0" y1="42" x2="300" y2="42"/>
    </g>
  </svg>
</section>

</body>
</html>
```